Upmarket Dessert Lounge needs a Business Card Design

We are an upmarket dessert lounge needing a business card to match our image.

We want something that is simple yet beautiful, feminine, classy, sophisticated and elegant. We want it to stand out and don't mind if it is bold.

The design should include our logo and colours of red or maroon with gold highlights. We don't mind if black is used.

Marlow & Quince

Target Market(s)

For those who like to indulge or treat themselves and give in to their temptations on good quality desserts.

Industry/Entity Type

Business

Requirements
Must have
• Must include our logo and our name

Marlow & Quince

M & Q

```html
<!DOCTYPE html>
<html lang="en">
<head>
<meta charset="utf-8">
<title>Marlow &amp; Quince — Business Card</title>
<link rel="stylesheet" href="https://fonts.googleapis.com/css2?family=Tinos:wght@400;700&display=swap">
<style>
  :root {
    --maroon: #7a1518;
    --peach: #fdd39a;
    --card: #ffffff;
    --ink: #3a3a3a;
    --rule: #cfcfcf;
    --backdrop: #eeeae6;
  }
  * { box-sizing: border-box; margin: 0; padding: 0; }
  html, body { width: 1200px; height: 417px; overflow: hidden; }
  body {
    background: var(--backdrop);
    font-family: "Tinos", "Times New Roman", serif;
    color: var(--ink);
    position: relative;
  }
  .card {
    position: absolute;
    top: 61px;
    width: 515px;
    height: 294px;
    background: var(--card);
    border-radius: 14px;
    overflow: hidden;
    box-shadow: 0 2px 6px rgba(0,0,0,0.25);
  }
  .card--front { left: 54px; }
  .card--back { left: 630px; }
  .side-band {
    position: absolute;
    left: 0; top: 0;
    width: 17px; height: 100%;
    display: flex; flex-direction: column;
  }
  .side-band__top { flex: 0 0 202px; background: var(--maroon); }
  .side-band__bottom { flex: 1; background: var(--peach); border-top: 2px solid #fff; }
  .holder {
    position: absolute;
    top: 25px; left: 0; right: 0;
    text-align: center;
    color: var(--maroon);
    font-size: 18px;
    font-weight: 700;
  }
  .holder__title { font-weight: 400; font-size: 14px; color: var(--ink); }
  .brand-name {
    position: absolute;
    left: 17px; right: 0;
    top: 126px;
    text-align: center;
    color: var(--maroon);
    font-size: 27px;
    font-weight: 400;
    letter-spacing: 1px;
  }
  .contact {
    position: absolute;
    bottom: 14px;
    left: 51px;
    display: flex;
    font-size: 13.5px;
    line-height: 19px;
  }
  .contact__group { padding-right: 16px; }
  .contact__group + .contact__group {
    border-left: 1px solid var(--rule);
    padding-left: 12px;
  }
  .contact__line { display: flex; align-items: center; gap: 6px; }
  .contact__line svg { width: 10px; height: 10px; fill: var(--maroon); flex: none; }
  .web {
    position: absolute;
    top: 253px; left: 17px; right: 0;
    text-align: center;
    font-size: 13px;
    letter-spacing: 3px;
  }
</style>
</head>
<body>
  <section class="card card--front">
    <div class="side-band"><div class="side-band__top"></div><div class="side-band__bottom"></div></div>
    <p class="holder">YOUR NAME, <span class="holder__title">Title</span></p>
    <p class="brand-name">MARLOW &amp; QUINCE</p>
    <div class="contact">
      <div class="contact__group">
        <p>00, Complex name</p>
        <p>City, State 000 000</p>
      </div>
      <div class="contact__group">
        <p class="contact__line">
          <svg viewBox="0 0 10 10"><circle cx="5" cy="5" r="4.5" fill="none" stroke="#7a1518"/><path d="M3 2.5h1.2l.6 1.4-.8.6a4 4 0 0 0 1.5 1.5l.6-.8 1.4.6v1.2C5 7 3 5 3 2.5z"/></svg>
          +2348135550142
        </p>
        <p class="contact__line">
          <svg viewBox="0 0 10 10"><rect x="2.5" y="0.5" width="5" height="9" rx="1"/><rect x="3.4" y="1.5" width="3.2" height="5" fill="#fff"/></svg>
          +2348135550142
        </p>
      </div>
      <div class="contact__group">
        <p class="contact__line">
          <svg viewBox="0 0 10 10"><rect x="0.5" y="2" width="9" height="6"/><path d="M0.5 2L5 5.5 9.5 2" fill="none" stroke="#fff" stroke-width="0.8"/></svg>
          info@marlowquince.com
        </p>
        <p class="contact__line">
          <svg viewBox="0 0 10 10"><circle cx="5" cy="5" r="4.5"/><path d="M0.5 5h9M5 0.5c-2 2.5-2 6.5 0 9M5 0.5c2 2.5 2 6.5 0 9" fill="none" stroke="#fff" stroke-width="0.6"/></svg>
          www.marlowquince.com
        </p>
      </div>
    </div>
  </section>

  <section class="card card--back">
    <div class="side-band"><div class="side-band__top"></div><div class="side-band__bottom"></div></div>
    <p class="brand-name">MARLOW &amp; QUINCE</p>
    <p class="web">www.marlowquince.com</p>
  </section>
</body>
</html>
```